Design a New Business Card for Our Company

We are looking for fresh, unique, and a modern business card that reflects our roots as digital marketing agency focused on SEM.

Industry/Entity Type

Marketing

Contact Information for Business Card

looking for very unique out of the box designs. clean and modern that compliments our logo

Requirements
Must have
• colors should match our logo
• Front should have name, address, email, and phone/fax of the person, phone/fax are the same number
• back should have our url

```html
<!DOCTYPE html>
<html lang="en">
<head>
<meta charset="utf-8">
<title>Brightway Solutions – Business Card</title>
<link rel="stylesheet" href="https://fonts.googleapis.com/css2?family=Arimo:wght@400;700&display=swap">
<style>
  :root {
    --backdrop: #e6e6e4;
    --card-white: #ffffff;
    --card-black: #0b0b0b;
    --brand-blue: #5b95d6;
    --ink: #333333;
    --soft-grey: #b4b4b4;
    --band-grey: #c9c9c9;
    --muted: #9a9a9a;
  }
  * { margin: 0; padding: 0; box-sizing: border-box; }
  html, body {
    width: 1200px;
    height: 878px;
    overflow: hidden;
    background: var(--backdrop);
    font-family: "Arimo", Arial, sans-serif;
  }
  .canvas {
    width: 1200px;
    height: 878px;
    display: flex;
    align-items: center;
    justify-content: center;
    gap: 40px;
  }
  .card {
    position: relative;
    width: 540px;
    height: 309px;
    box-shadow: 0 10px 26px rgba(0,0,0,0.18);
    overflow: hidden;
  }

  /* Front side */
  .card-front { background: var(--card-white); color: var(--ink); }
  .front-details {
    position: absolute;
    left: 34px;
    top: 30px;
  }
  .person-name {
    font-size: 30px;
    font-weight: 400;
    color: var(--brand-blue);
    line-height: 1;
  }
  .person-title {
    font-size: 12px;
    margin-top: 8px;
  }
  .contact-list {
    list-style: none;
    margin-top: 22px;
    font-size: 14px;
    line-height: 1.55;
  }
  .contact-label {
    display: inline-block;
    width: 20px;
    color: var(--brand-blue);
  }
  .address-block {
    margin-top: 16px;
    font-size: 13px;
    line-height: 1.4;
  }
  .front-accent {
    position: absolute;
    right: 54px;
    top: 86px;
  }
  .front-band {
    position: absolute;
    left: 0;
    right: 0;
    bottom: 0;
    height: 22px;
    background: var(--band-grey);
  }

  /* Back side */
  .card-back {
    background: var(--card-black);
    display: flex;
    flex-direction: column;
    align-items: center;
    justify-content: center;
  }
  .brand-lockup {
    display: flex;
    align-items: center;
    gap: 14px;
  }
  .brand-name {
    font-size: 38px;
    font-weight: 700;
    color: #ffffff;
    letter-spacing: -0.5px;
  }
  .web-address {
    margin-top: 18px;
    font-size: 15px;
    letter-spacing: 4px;
    color: var(--muted);
  }
</style>
</head>
<body>
<main class="canvas">

  <section class="card card-front" aria-label="Business card front">
    <div class="front-details">
      <h1 class="person-name">Your Name</h1>
      <p class="person-title">Job Title</p>
      <ul class="contact-list">
        <li><span class="contact-label">P</span>101 1010</li>
        <li><span class="contact-label">F</span>101 1010</li>
        <li><span class="contact-label">E</span>services@brightway.com</li>
      </ul>
      <p class="address-block">
        Address<br>
        your address, 9 your address, your address<br>
        PO Box 101, your address
      </p>
    </div>
    <svg class="front-accent" width="120" height="120" viewBox="0 0 120 120" aria-hidden="true">
      <circle cx="60" cy="60" r="56" fill="var(--brand-blue)"/>
    </svg>
    <div class="front-band"></div>
  </section>

  <section class="card card-back" aria-label="Business card back">
    <div class="brand-lockup">
      <svg width="30" height="30" viewBox="0 0 30 30" aria-hidden="true">
        <circle cx="15" cy="15" r="14" fill="var(--brand-blue)"/>
      </svg>
      <span class="brand-name">Brightway Solutions</span>
    </div>
    <p class="web-address">www.webaddress.com</p>
  </section>

</main>
</body>
</html>
```